Financial Advisor Resource Firm needs business card design

Need business card design for company in Omaha NE called Meridale Circle. We provide resources to financial advisors....workshop programs, retirement analysis, and insurance planning. I would like to see designs that use grays, greens, black, and white colors. The final design should communicate 'collaboration' and be simple yet attractive to financial planning clients. I will attached our logo and another picture of a puzzle piece coming together. I would like the incorporate the puzzle picture somehow, maybe on the back somehow, with color or just the gray scale....OR, the picture be the front of the card with 'Meridale' definition on it (see upload) and then company logo, employee name, title, address on the back (see ppt uploaded). The following disclosure needs to be included somewhere- Advisory services offered through Stonebrook Assets, LLC.
Updates

I uploaded a svg and ai file of the logo

Target Market(s)

Financial planning clients and financial advisors....so pretty diverse age range of about 40-70.

Industry/Entity Type

Financial Planning

Contact Information for Business Card

Tobias L. Fenwright, MBA
Founder/President
5287 E. Larkin Road
Suite 230
Omaha, NE 68190
Phone- (402) 555-0147
Cell- (402) 555-0183
Fax- (402) 555-0129
email- tobias@meridaleplan.example
web address- www.meridaleplan.example

Colors
1b1b1b
474747
d3d3d3
ffffff
9bcb3c
abd036

Requirements
Must have
• Must include logo provided, must be 2 sided, and must have disclosure...all of these items listed in project description

```html
<!DOCTYPE html>
<html lang="en">
<head>
<meta charset="utf-8">
<title>Meridale Circle — Business Card</title>
<link href="https://fonts.googleapis.com/css2?family=Montserrat:wght@400;500&display=swap" rel="stylesheet">
<style>
  :root {
    --stage: #f2f2f2;
    --card: #231f20;
    --green: #8cc63f;
    --white: #ffffff;
    --muted: #a8a8a8;
  }
  * { margin: 0; padding: 0; box-sizing: border-box; }
  html, body { width: 1200px; height: 900px; overflow: hidden; }
  body {
    position: relative;
    background: var(--stage);
    font-family: "Montserrat", Arial, sans-serif;
    color: var(--white);
  }
  .card {
    position: absolute;
    left: 305px;
    width: 591px;
    height: 338px;
    background: var(--card);
    overflow: hidden;
    box-shadow: 0 14px 24px rgba(0,0,0,0.22);
  }
  .card--front { top: 96px; }
  .card--back { top: 482px; }

  .card__art { position: absolute; inset: 0; }

  .brand {
    position: absolute;
    display: flex;
    align-items: center;
    gap: 8px;
  }
  .brand__dot {
    width: 13px; height: 13px;
    border-radius: 50%;
    background: var(--green);
    flex: none;
  }
  .brand__name {
    font-size: 17px;
    font-weight: 500;
    letter-spacing: 1.3px;
    color: var(--white);
    text-transform: uppercase;
    white-space: nowrap;
  }
  .card--front .brand { left: 19px; width: 240px; justify-content: center; top: 44px; }
  .card--back .brand { right: 31px; top: 50px; }

  .tagline {
    position: absolute;
    left: 19px; top: 89px;
    width: 240px;
    text-align: center;
    font-size: 14.5px;
    line-height: 19px;
    white-space: nowrap;
  }

  .rule { position: absolute; height: 2px; width: 44px; }
  .rule--white { background: var(--white); }
  .rule--green { background: var(--green); }

  .person { position: absolute; left: 30px; top: 118px; }
  .person__name { font-size: 18px; color: var(--green); }
  .person__name span { font-size: 14px; color: var(--white); }
  .person__title { font-size: 13px; margin-top: 2px; }

  .contacts { position: absolute; left: 30px; top: 180px; list-style: none; }
  .contacts li {
    display: flex; align-items: center;
    height: 25.5px;
    font-size: 14.5px;
  }
  .contacts svg { width: 16px; height: 16px; margin-right: 12px; fill: var(--green); }
  .accent { color: var(--green); }

  .address {
    position: absolute;
    left: 354px; top: 266px;
    font-style: normal;
    font-size: 14.5px;
    line-height: 20.5px;
    color: var(--green);
    white-space: nowrap;
  }

  .disclosure {
    position: absolute;
    left: 0; right: 0; bottom: 6px;
    text-align: center;
    font-size: 7.5px;
    letter-spacing: 0.2px;
    color: var(--muted);
  }
</style>
</head>
<body>

<section class="card card--front">
  <svg class="card__art" viewBox="0 0 591 338" preserveAspectRatio="none" role="img" aria-label="Grayscale photo of several hands joining puzzle pieces together">
    <defs>
      <linearGradient id="photoTone" x1="0" y1="0" x2="1" y2="1">
        <stop offset="0" stop-color="#e6e6e6"/>
        <stop offset="0.55" stop-color="#9a9a9a"/>
        <stop offset="1" stop-color="#474747"/>
      </linearGradient>
    </defs>
    <polygon points="305,0 591,0 591,338 185,338" fill="url(#photoTone)"/>
    <polygon points="299,0 306,0 191,338 184,338" fill="var(--green)"/>
  </svg>
  <div class="brand">
    <span class="brand__dot"></span>
    <span class="brand__name">Meridale Circle</span>
  </div>
  <p class="tagline">To come together and unite<br>in common interest and focus</p>
  <div class="rule rule--white" style="left:123px; top:146px;"></div>
  <div class="rule rule--green" style="left:112px; top:151px;"></div>
</section>

<section class="card card--back">
  <div class="brand">
    <span class="brand__dot"></span>
    <span class="brand__name">Meridale Circle</span>
  </div>
  <div class="rule rule--green" style="left:44px; top:88px;"></div>
  <div class="rule rule--white" style="left:33px; top:93px;"></div>

  <div class="person">
    <p class="person__name">Tobias L. Fenwright<span>, MBA</span></p>
    <p class="person__title">Founder | President</p>
  </div>

  <ul class="contacts">
    <li><svg viewBox="0 0 16 16"><path d="M3.6 1.2l2.3 2.6-1.3 1.9c.9 2 2.5 3.6 4.5 4.6l1.9-1.4 2.6 2.3-1.2 2.6C7.6 13.6 2.4 8.4 1 3.1z"/></svg>(402) 555 - 0147</li>
    <li><svg viewBox="0 0 16 16"><path d="M4 1h8v14H4zM5.5 2.5v9h5v-9zM7 12.5v1h2v-1z" fill-rule="evenodd"/></svg>(402) 555 - 0183</li>
    <li><svg viewBox="0 0 16 16"><path d="M1 5h3v10H1zM5 3h6l3 3v9H5zM7 8h2v2H7zm3 0h2v2h-2zm-3 3h2v2H7zm3 0h2v2h-2z" fill-rule="evenodd"/></svg>(402) 555 - 0129</li>
    <li><svg viewBox="0 0 16 16"><path d="M1 3h14v1.5L8 9 1 4.5zM1 6.3l7 4.5 7-4.5V13H1z"/></svg>tobias@meridaleplan.example</li>
    <li><svg viewBox="0 0 16 16"><circle cx="8" cy="8" r="7"/><path d="M5 4c1 1 2 1 2 2.5S5 8 5 9.5s1.5 1.5 1 3.5M10 3c0 1.5 1.5 2 2.5 2M10.5 11c1 0 2-1 2.5-2" stroke="#231f20" stroke-width="1.2" fill="none"/></svg>www.<span class="accent">meridaleplan</span>.example</li>
  </ul>

  <div class="rule rule--white" style="right:31px; top:235px;"></div>
  <div class="rule rule--green" style="right:42px; top:240px;"></div>

  <address class="address">
    5287 E. Larkin Road<br>
    Suite 230, Omaha, NE 68190
  </address>

  <p class="disclosure">Advisory services offered through Stonebrook Assets, LLC.</p>
</section>

</body>
</html>
```